"Leibeswerkstatt" private practice for physiotherapy

we are looking for a flyer design for a private practice for physiotherapy. the name of the practice is "Leibeswerkstatt".
Treatments such as: manual therapy, manual lymphatic drainage, classic massage, sectoral alternative practitioners are offered

The flyers should be double-sided and the format DIN long (105x210 mm)

Font styles to use
Serif

Colors
0094D4
00A9DD
6FCCEA
C7EBF8
E9F6FB

Requirements
Must have
• Leibeswerkstatt, Lindenweg 17, 06548 Sangerhausen / Leibeswerkstatt-beispielort.de / Tel. 03464 7183520

```html
<!DOCTYPE html>
<html lang="de">
<head>
<meta charset="utf-8">
<title>Leibeswerkstatt – Flyer DIN lang</title>
<link rel="stylesheet" href="https://fonts.googleapis.com/css2?family=Barlow+Semi+Condensed:wght@700&family=Oswald:wght@500&family=Mulish:wght@600;800;900&display=swap">
<style>
  :root{
    --stage:#02131c;
    --paper:#f4f5f7;
    --paper-shade:#e6e8ec;
    --blue-bright:#00a0dd;
    --blue-mid:#0f5db8;
    --blue-deep:#1f2f86;
    --navy:#1b2a86;
    --title-blue:#0f55b0;
    --white:#ffffff;
    --map-grey:#dfe3e6;
    --map-frame:#9aa0a6;
  }
  *{box-sizing:border-box;margin:0;padding:0}
  html,body{width:1200px;height:1200px;overflow:hidden;background:var(--stage)}
  .stage{position:relative;width:1200px;height:1200px}
  .flyer{position:absolute;top:180px;width:420px;height:840px;overflow:hidden;background:var(--paper)}
  .flyer--back{left:150px;background:linear-gradient(180deg,var(--white),var(--paper-shade))}
  .flyer--front{left:630px;background:var(--paper)}
  .flyer svg.shapes{position:absolute;inset:0}
  .brand{position:absolute;left:0;right:0;text-align:center;font-family:"Barlow Semi Condensed",sans-serif;font-weight:700;letter-spacing:-.5px}
  .flyer--back .brand{top:38px;font-size:46px;color:var(--title-blue)}
  .flyer--front .brand{top:40px;font-size:48px;color:var(--white)}
  .services{position:absolute;list-style:none;font-family:"Oswald",sans-serif;font-weight:500;color:var(--white);text-transform:uppercase;font-size:27px;line-height:38px}
  .services li{position:relative;padding-left:36px}
  .services li.cont{padding-left:36px}
  .tick{position:absolute;left:0;top:8px;width:24px;height:24px}
  .flyer--back .services{top:180px;left:58px}
  .flyer--front .services{top:510px;left:52px;font-size:29px;line-height:40px}
  .map{position:absolute;left:68px;top:470px;width:290px;height:180px;background:var(--map-grey);border:4px solid var(--map-frame)}
  .contact{position:absolute;left:0;right:0;text-align:center;font-family:"Mulish",sans-serif;color:var(--navy)}
  .address{top:672px;font-weight:800;font-size:28px;line-height:34px}
  .web{font-weight:600;font-size:17px}
  .flyer--back .web{top:748px}
  .flyer--front .web{top:770px}
  .phone{font-weight:900;letter-spacing:1px}
  .flyer--back .phone{top:772px;font-size:38px}
  .flyer--front .phone{top:792px;font-size:42px}
</style>
</head>
<body>
<main class="stage">

  <!-- Back side -->
  <section class="flyer flyer--back">
    <svg class="shapes" viewBox="0 0 420 840" width="420" height="840">
      <defs>
        <linearGradient id="backBlob" x1="0" y1="0" x2="1" y2="1">
          <stop offset="0" stop-color="var(--blue-bright)"/>
          <stop offset=".55" stop-color="var(--blue-mid)"/>
          <stop offset="1" stop-color="var(--blue-deep)"/>
        </linearGradient>
      </defs>
      <path role="img" aria-label="Blue wave with a faint treatment photo behind the service list"
            d="M0 150 C80 110 160 140 240 122 C320 104 380 60 420 88 L420 360 C380 420 300 470 200 460 C120 452 60 420 0 440 Z"
            fill="url(#backBlob)"/>
    </svg>
    <h1 class="brand">Leibeswerkstatt</h1>
    <ul class="services">
      <li><svg class="tick" viewBox="0 0 24 24"><circle cx="12" cy="12" r="10" fill="none" stroke="#fff" stroke-width="2"/><path d="M7 12l4 4 9-10" fill="none" stroke="#fff" stroke-width="2.5"/></svg>Manual therapy</li>
      <li><svg class="tick" viewBox="0 0 24 24"><circle cx="12" cy="12" r="10" fill="none" stroke="#fff" stroke-width="2"/><path d="M7 12l4 4 9-10" fill="none" stroke="#fff" stroke-width="2.5"/></svg>Classic massage</li>
      <li><svg class="tick" viewBox="0 0 24 24"><circle cx="12" cy="12" r="10" fill="none" stroke="#fff" stroke-width="2"/><path d="M7 12l4 4 9-10" fill="none" stroke="#fff" stroke-width="2.5"/></svg>Sectoral alternative</li>
      <li class="cont">practitioners</li>
      <li><svg class="tick" viewBox="0 0 24 24"><circle cx="12" cy="12" r="10" fill="none" stroke="#fff" stroke-width="2"/><path d="M7 12l4 4 9-10" fill="none" stroke="#fff" stroke-width="2.5"/></svg>Manual lymphatic</li>
      <li class="cont">drainage</li>
    </ul>
    <div class="map" role="img" aria-label="Street map showing the practice location"></div>
    <p class="contact address">Lindenweg 17<br>06548 Sangerhausen</p>
    <p class="contact web">Leibeswerkstatt-beispielort.de</p>
    <p class="contact phone">03464 7183520</p>
  </section>

  <!-- Front side -->
  <section class="flyer flyer--front">
    <svg class="shapes" viewBox="0 0 420 840" width="420" height="840">
      <defs>
        <linearGradient id="frontTop" x1="0" y1="0" x2="1" y2="1">
          <stop offset="0" stop-color="var(--blue-mid)"/>
          <stop offset="1" stop-color="var(--blue-deep)"/>
        </linearGradient>
        <linearGradient id="frontBlob" x1="0" y1="0" x2="1" y2="1">
          <stop offset="0" stop-color="var(--blue-mid)"/>
          <stop offset="1" stop-color="var(--blue-deep)"/>
        </linearGradient>
        <linearGradient id="photoTone" x1="0" y1="0" x2="1" y2="1">
          <stop offset="0" stop-color="#e9e4de"/>
          <stop offset=".5" stop-color="#c79a80"/>
          <stop offset="1" stop-color="#eceae7"/>
        </linearGradient>
      </defs>
      <path d="M0 0 H420 V215 C380 200 340 222 316 252 L110 330 C66 344 30 326 0 300 Z" fill="url(#frontTop)"/>
      <path d="M0 520 C60 470 160 462 262 500 C330 526 380 500 420 470 V640 C380 720 300 770 200 762 C120 754 60 742 0 762 Z" fill="url(#frontBlob)"/>
      <circle cx="210" cy="300" r="168" fill="var(--white)"/>
      <circle role="img" aria-label="Photo of a therapist treating a patient's shoulder" cx="210" cy="300" r="160" fill="url(#photoTone)"/>
    </svg>
    <h1 class="brand">Leibeswerkstatt</h1>
    <ul class="services">
      <li><svg class="tick" viewBox="0 0 24 24"><circle cx="12" cy="12" r="10" fill="none" stroke="#fff" stroke-width="2"/><path d="M7 12l4 4 9-10" fill="none" stroke="#fff" stroke-width="2.5"/></svg>Manual therapy</li>
      <li><svg class="tick" viewBox="0 0 24 24"><circle cx="12" cy="12" r="10" fill="none" stroke="#fff" stroke-width="2"/><path d="M7 12l4 4 9-10" fill="none" stroke="#fff" stroke-width="2.5"/></svg>Classic massage</li>
      <li><svg class="tick" viewBox="0 0 24 24"><circle cx="12" cy="12" r="10" fill="none" stroke="#fff" stroke-width="2"/><path d="M7 12l4 4 9-10" fill="none" stroke="#fff" stroke-width="2.5"/></svg>Sectoral alternative</li>
      <li class="cont">practitioners</li>
      <li><svg class="tick" viewBox="0 0 24 24"><circle cx="12" cy="12" r="10" fill="none" stroke="#fff" stroke-width="2"/><path d="M7 12l4 4 9-10" fill="none" stroke="#fff" stroke-width="2.5"/></svg>Manual lymphatic</li>
      <li class="cont">drainage</li>
    </ul>
    <p class="contact web">Leibeswerkstatt-beispielort.de</p>
    <p class="contact phone">03464 7183520</p>
  </section>

</main>
</body>
</html>
```